RWT Fittings Ltd Business Cards

We need a business card with our business logo. We provide window and door installations on high-rises in west coast British Colombia, Canada.

I would like my business information and details on one side of the card, and the other side the company name with logo

Target Market(s)

General Contractors

Industry/Entity Type

Construction

Contact Information for Business Card

one side i want my company name and logo in the dark theme logo that i provided

Requirements
Must have
• Marco Peltieri, 16045518293, RWTFittings@mailbox-demo.com, 1407-5194 Linden Row Burnaby BC, V5H 2K9, Owner & Manager

```html
<!DOCTYPE html>
<html lang="en">
<head>
<meta charset="utf-8">
<title>RWT Fittings Ltd — Business Cards</title>
<link rel="stylesheet" href="https://fonts.googleapis.com/css2?family=Montserrat:wght@600;800&family=Roboto:wght@400;500&display=swap">
<style>
  :root {
    --page: #232323;
    --card-dark: #1e1f22;
    --edge-blue: #2aa8e4;
    --brand-blue: #2ba9e1;
    --name-grey: #9a9a9c;
    --text-white: #f2f2f2;
    --photo-deep: #1f1d1b;
    --photo-warm: #4a443e;
  }
  * { box-sizing: border-box; margin: 0; padding: 0; }
  html, body { width: 1200px; height: 780px; overflow: hidden; background: var(--page); }
  .sheet {
    width: 1200px; height: 780px;
    display: flex; align-items: center; justify-content: center; gap: 48px;
  }
  .card {
    position: relative;
    width: 540px; height: 308px;
    border-radius: 18px;
    border: 4px solid var(--edge-blue);
    overflow: hidden;
    box-shadow: 0 14px 30px rgba(0,0,0,.55);
  }
  .card--front .office-photo {
    position: absolute; inset: 0;
    background: radial-gradient(ellipse at 70% 35%, var(--photo-warm) 0%, #35312d 45%, var(--photo-deep) 100%);
  }
  .brand {
    position: absolute;
    display: flex; align-items: center; gap: 12px;
    font-family: "Montserrat", sans-serif; font-weight: 800;
    color: var(--brand-blue);
    letter-spacing: 1px;
    white-space: nowrap;
  }
  .brand__square { display: block; background: var(--brand-blue); }
  .card--front .brand { left: 50%; top: 50%; transform: translate(-50%, -50%); font-size: 38px; }
  .card--front .brand__square { width: 34px; height: 34px; }

  .card--back { background: var(--card-dark); }
  .card--back .brand { left: 26px; top: 40px; font-size: 28px; }
  .card--back .brand__square { width: 26px; height: 26px; }

  .person {
    position: absolute; right: 44px; top: 104px;
    text-align: right;
  }
  .person__name {
    font-family: "Montserrat", sans-serif; font-weight: 800; font-size: 30px; line-height: 1;
  }
  .person__first { color: var(--brand-blue); }
  .person__last { color: var(--name-grey); }
  .person__role {
    margin-top: 4px;
    font-family: "Montserrat", sans-serif; font-weight: 600; font-size: 14px;
    color: var(--text-white);
  }
  .accent-bar {
    position: absolute; right: 0; top: 88px;
    width: 22px; height: 62px; background: var(--brand-blue);
  }
  .contact {
    position: absolute; left: 30px; bottom: 26px;
    font-family: "Roboto", sans-serif; font-size: 15px; line-height: 1.35;
    color: var(--text-white);
  }
  .contact__address { margin-bottom: 12px; }
  .contact__row { display: flex; align-items: center; gap: 8px; }
  .contact__row svg { width: 16px; height: 16px; flex: none; }
</style>
</head>
<body>
<main class="sheet">
  <section class="card card--front">
    <div class="office-photo" role="img" aria-label="Dimly lit office interior with a plant, softly blurred"></div>
    <div class="brand"><span class="brand__square"></span>RWT Fittings Ltd</div>
  </section>

  <section class="card card--back">
    <div class="brand"><span class="brand__square"></span>RWT Fittings Ltd</div>
    <div class="accent-bar"></div>
    <div class="person">
      <div class="person__name"><span class="person__first">Marco</span> <span class="person__last">Peltieri</span></div>
      <div class="person__role">Owner &amp; Manager</div>
    </div>
    <div class="contact">
      <p class="contact__address">1407-5194 Linden Row<br>Burnaby BC, V5H 2K9</p>
      <p class="contact__row">
        <svg viewBox="0 0 24 24" aria-hidden="true"><path fill="#2ba9e1" d="M6.6 10.8a15.1 15.1 0 0 0 6.6 6.6l2.2-2.2a1 1 0 0 1 1-.25 11.4 11.4 0 0 0 3.6.57 1 1 0 0 1 1 1V20a1 1 0 0 1-1 1A17 17 0 0 1 3 4a1 1 0 0 1 1-1h3.5a1 1 0 0 1 1 1c0 1.25.2 2.45.57 3.57a1 1 0 0 1-.25 1z"/></svg>
        1604 551 8293
      </p>
      <p class="contact__row">
        <svg viewBox="0 0 24 24" aria-hidden="true"><rect x="2" y="5" width="20" height="14" rx="2" fill="none" stroke="#2ba9e1" stroke-width="2"/><path d="M3 6l9 7 9-7" fill="none" stroke="#2ba9e1" stroke-width="2"/></svg>
        RWTFittings@mailbox-demo.com
      </p>
    </div>
  </section>
</main>
</body>
</html>
```